A start-up named "Corvane Therapeutics" - needs a new PowerPoint design

We need a new PowerPoint Design for an early-stage start-up named "Corvane Therapeutics" seeking to disrupt the current approach towards drug discovery within aging disorders.

We would like to build on Corvane's legacy, the founder of the modern science of genetics, by employing a multidisciplinary approach, experimenting, and providing elderly patients the attention they deserve.

We have selected the suffix "therapeutics" intentionally as it stands for (a medicine) the treatment of disease; the science of healing. Alzheimer’s treatment is a huge, urgent, unmet need:
- Shift from a disease-management system to a preventive medicine system
- Focus on increasing the health span, not only the life span

Target Market(s)

Pharma/ Biotech Executives Medical Institutions Healthcare professionals (MDs, nurses, payors, pharmacists, etc.) Patients

Industry/Entity Type

Healthcare

Other font styles liked:
• Celias

Colors
0054AA
0677BA
7BADD7
CADEEF
E8F1F8
E54698
E96AAD
F1A4CE
F9D9EA
FCEFF6
A7469A
B969AE
D3A5CF
EDDBEB
F8F0F9
6B429C
8869AF
B7A5CE
E3DAEB
F3F0F8

Requirements
Must have
• - differentiate from other companies named after Corvane - differentiate from other Pharma/ Biotech companies
Nice to have
• simplicity/ minimalist logo vivid colors gradient 3D Life-Sciences inspired Simple geometry Balance
Should not have
• mascot/ emblem watermark logo animated ink style nature-inspired inventive typography artistic chaos

```html
<!DOCTYPE html>
<html lang="en">
<head>
<meta charset="utf-8">
<title>Corvane Therapeutics – Presentation Slides</title>
<link rel="stylesheet" href="https://fonts.googleapis.com/css2?family=Josefin+Sans:wght@600;700&family=Montserrat:wght@400;500&display=swap">
<style>
  :root{
    --page:#444444;
    --sky:#14a3e3;
    --blue:#1b7fd6;
    --indigo:#4a4bb8;
    --violet:#7c1e98;
    --magenta:#8a1a8a;
    --cyan:#1ba0e2;
    --ink:#333333;
    --white:#ffffff;
    --brand:#2a6fc0;
    --head:"Josefin Sans", sans-serif;
    --body:"Montserrat", sans-serif;
  }
  *{margin:0;padding:0;box-sizing:border-box}
  html,body{width:1200px;height:3413px;overflow:hidden;background:var(--page)}
  body{position:relative;font-family:var(--body);color:var(--white)}
  .slide{position:absolute;left:50px;width:1103px;height:621px;overflow:hidden}
  .gradient{background:linear-gradient(90deg,var(--sky) 0%,var(--blue) 38%,var(--indigo) 62%,var(--violet) 100%)}
  .white{background:var(--white);color:var(--ink)}
  .abs{position:absolute}

  /* slide 1 */
  .s1{top:50px}
  .hero-title{left:105px;top:158px;font:700 55px/62px var(--head);letter-spacing:.5px}
  .hero-text{left:105px;top:357px;width:560px;font-size:10px;line-height:29px;white-space:normal}
  .social{left:107px;top:450px;display:flex;gap:7px}
  .social span{width:26px;height:26px;border-radius:50%;background:var(--white)}
  .site{left:0;width:1103px;top:575px;text-align:center;font-size:9px;letter-spacing:2px}
  .mark-name{font:700 46px/1 var(--head);color:var(--white);text-align:center;display:flex;align-items:center;justify-content:center}

  /* slide 2 */
  .s2{top:715px}
  .slide-title{left:138px;top:50px;font:700 40px/46px var(--head)}
  .brand-small{font:600 22px/1 var(--head);white-space:nowrap}
  .point{width:260px}
  .point h3{font:700 16px/20px var(--head);margin-bottom:14px;white-space:nowrap}
  .point p{font-size:10px;line-height:20px}
  .num{font:700 92px/1 var(--head);color:rgba(255,255,255,.09)}

  /* slide 3 */
  .s3{top:1377px}
  .about-title{left:588px;top:128px;font:700 27px/30px var(--head);color:var(--cyan);white-space:nowrap}
  .about-rule{left:588px;top:166px;width:127px;height:3px;background:var(--magenta)}
  .about-text{left:588px;top:199px;width:472px;font-size:9.6px;line-height:23.5px;text-align:justify;color:var(--ink)}

  /* slide 4 */
  .s4{top:2041px}
  .attr h3{font:700 19px/22px var(--head);color:var(--magenta)}
  .attr p{font-size:8.5px;line-height:17px;color:var(--ink);width:410px;margin-top:3px}

  /* slide 5 */
  .s5{top:2703px}
  .thanks-title{left:106px;top:116px;font:700 35px/40px var(--head)}
  .thanks-text{left:106px;top:162px;width:390px;font-size:10px;line-height:20px}
  .contact{left:106px;top:280px;font-size:14.5px}
  .contact li{list-style:none;display:flex;align-items:center;height:41px}
  .contact li.cont{padding-left:29px}
  .contact svg{width:16px;height:16px;margin-right:13px;flex:none}
  .divider{left:570px;top:113px;width:1px;height:396px;background:rgba(255,255,255,.7)}
</style>
</head>
<body>

<!-- Slide 1: welcome -->
<section class="slide gradient s1">
  <h1 class="abs hero-title">WELCOME TO<br>CORVANE<br>THERAPEUTICS</h1>
  <p class="abs hero-text">Lorem ipsum dolor sit amet, consectetur adipiscing elit, sed do eiusmod tempor incididunt<br>ut labore et dolore magna aliqua. Quis ipsum suspendisse ultrices gravida. Risus commodo<br>viverra maecenas accumsan lacus vel facilisis.</p>
  <div class="abs social"><span></span><span></span><span></span><span></span></div>
  <div class="abs mark-name" style="left:652px;top:69px;width:348px;height:351px">Corvane</div>
  <p class="abs site">WWW.CORVANETHERAPEUTICS.COM</p>
</section>

<!-- Slide 2: six points -->
<section class="slide gradient s2">
  <svg class="abs" style="left:0;top:0" width="40" height="140" viewBox="0 0 40 140"><polygon points="0,16 34,73 0,130" fill="#fff"/></svg>
  <h2 class="abs slide-title">LOREM IPSUM DOLOR</h2>
  <div class="abs brand-small" style="left:873px;top:50px;width:184px;text-align:right">Corvane Therapeutics</div>

  <span class="abs num" style="left:29px;top:160px">1</span>
  <span class="abs num" style="left:376px;top:160px">2</span>
  <span class="abs num" style="left:724px;top:160px">3</span>
  <span class="abs num" style="left:29px;top:384px">4</span>
  <span class="abs num" style="left:376px;top:384px">5</span>
  <span class="abs num" style="left:724px;top:384px">6</span>

  <div class="abs point" style="left:94px;top:155px"><h3>LOREM IPSUM DOLOR SIT AM</h3><p>Lorem ipsum dolor sit amet, consectetur adipiscing elit, sed do eiusmod tempor incididunt ut labore et dolore magna aliqua. Ut enim ad minim veniam, quis nostrud exercitation ullamco laboris nisi ut aliquip ex ea commodo consequat.</p></div>
  <div class="abs point" style="left:441px;top:155px"><h3>LOREM IPSUM DOLOR SIT AM</h3><p>Lorem ipsum dolor sit amet, consectetur adipiscing elit, sed do eiusmod tempor incididunt ut labore et dolore magna aliqua. Ut enim ad minim veniam, quis nostrud exercitation ullamco laboris nisi ut aliquip ex ea commodo consequat.</p></div>
  <div class="abs point" style="left:784px;top:155px"><h3>LOREM IPSUM DOLOR SIT AM</h3><p>Lorem ipsum dolor sit amet, consectetur adipiscing elit, sed do eiusmod tempor incididunt ut labore et dolore magna aliqua. Ut enim ad minim veniam, quis nostrud exercitation ullamco laboris nisi ut aliquip ex ea commodo consequat.</p></div>
  <div class="abs point" style="left:94px;top:379px"><h3>LOREM IPSUM DOLOR SIT AM</h3><p>Lorem ipsum dolor sit amet, consectetur adipiscing elit, sed do eiusmod tempor incididunt ut labore et dolore magna aliqua. Ut enim ad minim veniam, quis nostrud exercitation ullamco laboris nisi ut aliquip ex ea commodo consequat.</p></div>
  <div class="abs point" style="left:441px;top:379px"><h3>LOREM IPSUM DOLOR SIT AM</h3><p>Lorem ipsum dolor sit amet, consectetur adipiscing elit, sed do eiusmod tempor incididunt ut labore et dolore magna aliqua. Ut enim ad minim veniam, quis nostrud exercitation ullamco laboris nisi ut aliquip ex ea commodo consequat.</p></div>
  <div class="abs point" style="left:790px;top:379px"><h3>LOREM IPSUM DOLOR SIT AM</h3><p>Lorem ipsum dolor sit amet, consectetur adipiscing elit, sed do eiusmod tempor incididunt ut labore et dolore magna aliqua. Ut enim ad minim veniam, quis nostrud exercitation ullamco laboris nisi ut aliquip ex ea commodo consequat.</p></div>
</section>

<!-- Slide 3: about -->
<section class="slide white s3">
  <svg class="abs" style="left:0;top:0" width="570" height="621" viewBox="0 0 570 621">
    <defs>
      <linearGradient id="photoTone" x1="0" y1="0" x2="1" y2="1">
        <stop offset="0" stop-color="#1d3a5c"/><stop offset=".6" stop-color="#2c3440"/><stop offset="1" stop-color="#7a5a44"/>
      </linearGradient>
      <linearGradient id="edgeTone" x1="0" y1="0" x2="0" y2="1">
        <stop offset="0" stop-color="#1b7fd6"/><stop offset="1" stop-color="#7c1e98"/>
      </linearGradient>
    </defs>
    <polygon role="img" aria-label="Photo of an elderly man holding his head, fragments drifting away from it, suggesting memory loss" points="0,0 507,0 558,291 502,621 0,621" fill="url(#photoTone)"/>
    <polyline points="507,0 558,291 502,621" fill="none" stroke="url(#edgeTone)" stroke-width="5"/>
  </svg>
  <div class="abs brand-small" style="left:881px;top:30px;width:204px;text-align:right;color:var(--brand)">Corvane Therapeutics</div>
  <h2 class="abs about-title">ABOUT CORVANE THERAPEUTICS</h2>
  <div class="abs about-rule"></div>
  <p class="abs about-text">Lorem ipsum dolor sit amet, consectetur adipiscing elit, sed do eiusmod tempor incididunt ut labore et dolore magna aliqua. Quis ipsum suspendisse ultrices gravida. Risus commodo viverra maecenas accumsan lacus vel facilisis. Sed ut perspiciatis unde omnis iste natus error sit voluptatem ccusantium doloremque laudantium, totam rem aperiam, eaque ipsa quae ab illo inventore veritatis et quasi architecto beatae vitae dicta sunt explicabo. Nemo enim ipsam voluptatem quia voluptas sit pernatur aut odit aut fugit, sed quia consequuntur magni dolores eos qui ratione voluptatem sequi nesciunt. Neque porro quisquam est, qui dolorem ipsum quia dolor sit amet, consectetur, adipisci velit, sed quia non numquam eius modi tempora incidunt ut labore et dolore magnam aliquam quaerat voluptatem. Ut enim ad minima veniam, quis nostrum exercitationem ullam corporis suscipit laboriosam, nisi ut aliquid ex ea commodi consequatur Lorem ipsum dolor sit amet, consectetur adipiscing elit, sed do eiusmod tempor incididunt ut labore et dolore magna aliqua. Quis ipsum suspendisse ultrices gravida. Risus commodo viverra maecenas accumsan lacus vel facilisis. Sed ut perspiciatis unde omnis iste natus error sit voluptatem ccusantium doloremque laudantium, totam rem aperiam, eaque ipsa quae ab illo inventore veritatis</p>
</section>

<!-- Slide 4: attributes -->
<section class="slide white s4">
  <div class="abs brand-small" style="left:881px;top:30px;width:204px;text-align:right;color:var(--brand)">Corvane Therapeutics</div>
  <div class="abs mark-name" style="left:105px;top:207px;width:273px;height:273px;color:var(--brand);font-size:44px">Corvane</div>

  <svg class="abs" style="left:0;top:0" width="1103" height="621" viewBox="0 0 1103 621">
    <defs>
      <g id="teamIcon" fill="none" stroke="#fff" stroke-width="1.4">
        <circle cx="0" cy="-4" r="3"/><path d="M-6,8 a6,6 0 0 1 12,0"/>
        <circle cx="-8" cy="-1" r="2.4"/><path d="M-13,9 a5,5 0 0 1 7,-5"/>
        <circle cx="8" cy="-1" r="2.4"/><path d="M13,9 a5,5 0 0 0 -7,-5"/>
      </g>
    </defs>
    <path d="M351,74 Q683,325 351,575" fill="none" stroke="#1ba0e2" stroke-width="1.5"/>
    <g fill="#bfe6f8"><circle cx="407" cy="102" r="32"/><circle cx="482" cy="191" r="32"/><circle cx="517" cy="277" r="32"/><circle cx="517" cy="363" r="32"/><circle cx="482" cy="449" r="32"/><circle cx="407" cy="535" r="32"/></g>
    <g fill="#1ba0e2"><circle cx="407" cy="102" r="25"/><circle cx="482" cy="191" r="25"/><circle cx="517" cy="277" r="25"/><circle cx="517" cy="363" r="25"/><circle cx="482" cy="449" r="25"/><circle cx="407" cy="535" r="25"/></g>
    <use href="#teamIcon" x="407" y="102"/><use href="#teamIcon" x="482" y="191"/><use href="#teamIcon" x="517" y="277"/>
    <use href="#teamIcon" x="517" y="363"/><use href="#teamIcon" x="482" y="449"/><use href="#teamIcon" x="407" y="535"/>
  </svg>

  <div class="abs attr" style="left:462px;top:71px"><h3>ATTRIBUTE 1</h3><p>Lorem ipsum dolor sit amet, consectetur adipiscing elit, sed do eiusmod tempor incididunt ut labore et dolore magna aliqua. Ut enim ad minim veniam, quis nostrud exercitation.</p></div>
  <div class="abs attr" style="left:536px;top:157px"><h3>ATTRIBUTE 2</h3><p>Lorem ipsum dolor sit amet, consectetur adipiscing elit, sed do eiusmod tempor incididunt ut labore et dolore magna aliqua. Ut enim ad minim veniam, quis nostrud exercitation.</p></div>
  <div class="abs attr" style="left:571px;top:243px"><h3>ATTRIBUTE 3</h3><p>Lorem ipsum dolor sit amet, consectetur adipiscing elit, sed do eiusmod tempor incididunt ut labore et dolore magna aliqua. Ut enim ad minim veniam, quis nostrud exercitation.</p></div>
  <div class="abs attr" style="left:571px;top:329px"><h3>ATTRIBUTE 4</h3><p>Lorem ipsum dolor sit amet, consectetur adipiscing elit, sed do eiusmod tempor incididunt ut labore et dolore magna aliqua. Ut enim ad minim veniam, quis nostrud exercitation.</p></div>
  <div class="abs attr" style="left:536px;top:415px"><h3>ATTRIBUTE 5</h3><p>Lorem ipsum dolor sit amet, consectetur adipiscing elit, sed do eiusmod tempor incididunt ut labore et dolore magna aliqua. Ut enim ad minim veniam, quis nostrud exercitation.</p></div>
  <div class="abs attr" style="left:462px;top:501px"><h3>ATTRIBUTE 6</h3><p>Lorem ipsum dolor sit amet, consectetur adipiscing elit, sed do eiusmod tempor incididunt ut labore et dolore magna aliqua. Ut enim ad minim veniam, quis nostrud exercitation.</p></div>
</section>

<!-- Slide 5: thank you -->
<section class="slide gradient s5">
  <h2 class="abs thanks-title">THANK YOU</h2>
  <p class="abs thanks-text">Sed ut perspiciatis unde omnis iste natus error sit voluptatem accusantium doloremque laudantium, totam rem aperiam, eaque ipsa quae ab illo inventore veritatis et quasi architecto beatae vitae dicta sunt explicabo. Nemo enim ipsam volutatem quia.</p>
  <ul class="abs contact">
    <li><svg viewBox="0 0 16 16"><path d="M3 1l3 3-1.5 2a9 9 0 0 0 5.5 5.5L12 10l3 3-2 2C7 15 1 9 1 3z" fill="#b0309f"/></svg>+1 888 8888 888</li>
    <li><svg viewBox="0 0 16 16"><circle cx="8" cy="8" r="6.5" fill="none" stroke="#b0309f" stroke-width="1.6"/><path d="M1.5 8h13M8 1.5c-3 3.5-3 9.5 0 13M8 1.5c3 3.5 3 9.5 0 13" fill="none" stroke="#b0309f" stroke-width="1.3"/></svg>www.corvanetherapeutics.com</li>
    <li><svg viewBox="0 0 16 16"><rect x="1" y="3" width="14" height="10" rx="1" fill="#b0309f"/><path d="M1.5 4l6.5 5 6.5-5" fill="none" stroke="#5a3fb0" stroke-width="1.2"/></svg>info@corvanetherapeutics.com</li>
    <li><svg viewBox="0 0 16 16"><path d="M8 1a5 5 0 0 0-5 5c0 4 5 9 5 9s5-5 5-9a5 5 0 0 0-5-5z" fill="#b0309f"/><circle cx="8" cy="6" r="1.8" fill="#3a6fd0"/></svg>123 Lorem ipsum dolor sit amet</li>
    <li class="cont">consectetur adipiscing elit</li>
    <li class="cont">sed do eiusmod tempor</li>
  </ul>
  <div class="abs divider"></div>
  <div class="abs mark-name" style="left:652px;top:122px;width:348px;height:349px">Corvane</div>
</section>

</body>
</html>
```